Business Card Design

We like to use greens as you will see in our logo (but not TOO much green). We are a Dental Clinic in a somewhat eccentric community. We do not like the dated sharp designs which we see many dentists use. We're looking for something bright and fresh while still maintaining the integrity of the profession. Elegance is not necessarily what we are going for... we need for the design to be "mature" but also up-lifting.

See our logo.
Updates

Project Deadline Extended
Reason: We have 5 designs which we like. But we'd like to see a few more before committing to a design.

Project Deadline Extended
Reason: We are awaiting revisions to this project. We are still welcoming designs while we wait to see if designers are able to provide to us the revisions we require in order to proceed with a selection.

Target Market(s)

Younger families - ages late 20's to early 40's

Industry/Entity Type

Business

Contact Information for Business Card

Corwel T. Banfry DDS 2730 W. Halvert Rd. Ste. 7 Royal Oak, MI 48391 (248)555-0174 FX (248)555-0189 info@BrightwellDentalCareMi.com BrigthwellDentalCareMi.com on the back of the card we need an appointment reminder (For____ Date___ Time____) with "If you are unable to keep your appointment, kindly give 48 hours notice" at the bottom. No use of teeth in the design. DOUBLE SIDED DESIGN

Requirements
Should not have
• The use of pictures of teeth

```html
<!DOCTYPE html>
<html lang="en">
<head>
<meta charset="utf-8">
<title>Brightwell Dental Care – Business Card</title>
<link rel="stylesheet" href="https://fonts.googleapis.com/css2?family=Open+Sans:ital,wght@0,400;0,600;0,700;1,400&family=Tinos:ital,wght@0,400;0,700;1,400&display=swap">
<style>
  :root {
    --backdrop: #ece9e4;
    --card: #ffffff;
    --green-dark: #2f7a17;
    --green-pill: #3a7d1c;
    --green-line: #9ccc55;
    --ink: #2b2b2b;
    --ink-soft: #555555;
    --rule: #b9b9b9;
  }
  * { margin: 0; padding: 0; box-sizing: border-box; }
  html, body { width: 1200px; height: 492px; overflow: hidden; }
  body {
    background: var(--backdrop);
    font-family: "Open Sans", Arial, sans-serif;
    color: var(--ink);
    position: relative;
  }
  .card {
    position: absolute;
    top: 96px;
    width: 500px;
    height: 300px;
    background: var(--card);
    border-radius: 26px;
    box-shadow: 0 4px 14px rgba(0,0,0,0.18);
    overflow: hidden;
  }
  .card--front { left: 70px; }
  .card--back { left: 630px; }

  /* Front */
  .name-pill {
    position: absolute;
    left: 112px; top: 28px;
    width: 270px; height: 42px;
    background: var(--green-pill);
    border-radius: 21px;
    color: #fff;
    font-weight: 700;
    font-size: 19px;
    line-height: 42px;
    text-align: center;
    white-space: nowrap;
  }
  .name-pill .degree { font-size: 13px; }
  .brand {
    position: absolute;
    display: flex;
    align-items: center;
    gap: 10px;
    color: var(--green-dark);
    font-weight: 600;
  }
  .brand__dot {
    width: 16px; height: 16px;
    border-radius: 50%;
    background: var(--green-line);
    flex: none;
  }
  .brand__name { line-height: 1.1; white-space: nowrap; }
  .card--front .brand { left: 40px; top: 190px; font-size: 22px; }
  .divider {
    position: absolute;
    left: 262px; top: 108px;
    width: 1px; height: 150px;
    background: var(--rule);
  }
  .contact {
    position: absolute;
    left: 274px; top: 110px;
    width: 210px;
    font-size: 11.5px;
    line-height: 1.5;
    color: var(--ink);
    white-space: nowrap;
  }
  .contact__address { margin-bottom: 14px; }
  .contact__row { display: flex; align-items: center; gap: 5px; }
  .contact__row svg { width: 11px; height: 11px; flex: none; }

  /* Back */
  .card--back .brand { left: 32px; top: 58px; font-size: 24px; }
  .appointment {
    position: absolute;
    left: 44px; top: 136px;
    right: 30px;
    font-family: "Tinos", "Times New Roman", serif;
  }
  .appointment__title {
    color: var(--green-dark);
    font-weight: 700;
    font-size: 15px;
    letter-spacing: 0.5px;
    border-bottom: 1px dotted var(--rule);
    padding-bottom: 2px;
    width: 350px;
  }
  .field-row {
    display: flex;
    align-items: flex-end;
    gap: 6px;
    font-family: "Open Sans", Arial, sans-serif;
    font-size: 14px;
    color: var(--ink-soft);
    margin-top: 16px;
    white-space: nowrap;
  }
  .field-line { border-bottom: 1px solid #8a8a8a; height: 14px; }
  .field-line--dotted { border-bottom-style: dotted; flex: 1; }
  .field-line--date { width: 90px; }
  .field-line--time { width: 86px; }
  .field-label--time { margin-left: 14px; }
  .note {
    margin-top: 18px;
    font-style: italic;
    font-size: 14.5px;
    color: var(--ink-soft);
    white-space: nowrap;
  }
</style>
</head>
<body>
  <section class="card card--front" aria-label="Business card front">
    <div class="name-pill">Corwel T. Banfry, <span class="degree">DDS</span></div>
    <div class="brand"><span class="brand__dot"></span><span class="brand__name">Brightwell<br>Dental Care</span></div>
    <div class="divider"></div>
    <div class="contact">
      <p class="contact__address">2730 W. Halvert Rd. Ste. 7<br>Royal Oak, MI 48391</p>
      <p class="contact__row">
        <svg viewBox="0 0 12 12" aria-hidden="true"><circle cx="6" cy="6" r="5.5" fill="none" stroke="currentColor"/><path d="M4 3.2l1 1.6-.7.7c.4.9 1.1 1.6 2 2l.7-.7 1.6 1-.5 1.1C5.8 9 3 6.2 2.9 3.7z" fill="currentColor"/></svg>
        (248)555-0174</p>
      <p class="contact__row">
        <svg viewBox="0 0 12 12" aria-hidden="true"><rect x="2" y="1" width="8" height="4" fill="none" stroke="currentColor"/><rect x="0.5" y="5" width="11" height="4.5" rx="1" fill="currentColor"/><rect x="3" y="8" width="6" height="3.5" fill="#fff" stroke="currentColor"/></svg>
        (248)555-0189</p>
      <p class="contact__row">
        <svg viewBox="0 0 12 12" aria-hidden="true"><rect x="0.5" y="2.5" width="11" height="7.5" fill="currentColor"/><path d="M0.5 2.5l5.5 4.5 5.5-4.5" fill="none" stroke="#fff"/></svg>
        info@BrightwellDentalCareMi.com</p>
      <p class="contact__row">
        <svg viewBox="0 0 12 12" aria-hidden="true"><circle cx="6" cy="6" r="5.5" fill="currentColor"/><path d="M0.5 6h11M6 .5v11M2 3h8M2 9h8" stroke="#fff" stroke-width="0.7"/></svg>
        www.BrigthwellDentalCareMi.com</p>
    </div>
  </section>

  <section class="card card--back" aria-label="Business card back">
    <div class="brand"><span class="brand__dot"></span><span class="brand__name">Brightwell<br>Dental Care</span></div>
    <div class="appointment">
      <h2 class="appointment__title">YOUR APPOINTMENT</h2>
      <div class="field-row"><span>Name :</span><span class="field-line field-line--dotted"></span></div>
      <div class="field-row">
        <span>Date :</span><span class="field-line field-line--date"></span>
        <span class="field-label--time">Time :</span><span class="field-line field-line--time"></span><span>am / pm</span>
      </div>
      <p class="note">If you are unable to keep your appointment, kindly give 48 hours notice</p>
    </div>
  </section>
</body>
</html>
```